Dental specialist needs a sharp looking letterhead

I am looking for a letterhead to be used to send letters and communication between myself (a dental specialist) and other dentists.
My office is a state of the art dental specialty office.
I need to letterhead to also state:
Bertram L. Oswick DDS
2748 Tollard Avenue, Suite K
West Tollard, NY 14391
(716)392-5061
fax: (716)392-5087
oswickroot.com (**this email address may change)

i included my logo designs.
thank you

Target Market(s)

dentists

Industry/Entity Type

Communication

Requirements
Must have
• the included logo, whether the vertical or horizontal versions

```html
<!DOCTYPE html>
<html lang="en">
<head>
<meta charset="utf-8">
<title>Meridian Endodontics P.C. – Letterhead</title>
<link rel="stylesheet" href="https://fonts.googleapis.com/css2?family=Bitter:wght@400&family=Raleway:wght@400&display=swap">
<style>
  :root {
    --ink: #1d1d1b;
    --text: #3a3a3a;
    --rule: #6b6b6b;
    --brand-blue: #43a3da;
    --brand-green: #8cc63f;
    --paper: #ffffff;
  }
  html, body {
    margin: 0;
    padding: 0;
    width: 931px;
    height: 1200px;
    overflow: hidden;
    background: var(--paper);
  }
  .letterhead {
    position: relative;
    width: 931px;
    height: 1200px;
    background: var(--paper);
    overflow: hidden;
  }
  .practice-name {
    position: absolute;
    left: 36px;
    top: 24px;
    display: flex;
    align-items: center;
    gap: 14px;
    font-family: "Bitter", Georgia, serif;
    font-weight: 400;
    color: var(--ink);
  }
  .practice-name__dot {
    width: 66px;
    height: 66px;
    border-radius: 50%;
    background: var(--brand-blue);
  }
  .practice-name__title {
    display: block;
    font-size: 36px;
    line-height: 38px;
    letter-spacing: -0.5px;
    text-transform: uppercase;
  }
  .practice-name__sub {
    display: block;
    font-size: 15px;
    line-height: 18px;
    letter-spacing: 2.2px;
    padding-left: 26px;
  }
  .address {
    position: absolute;
    right: 291px;
    top: 22px;
    margin: 0;
    text-align: right;
    font-family: "Raleway", Arial, sans-serif;
    font-style: normal;
    font-size: 15.5px;
    line-height: 26.5px;
    color: var(--text);
    letter-spacing: -0.3px;
  }
  .divider {
    position: absolute;
    left: 662px;
    top: 26px;
    width: 1px;
    height: 68px;
    background: var(--rule);
  }
  .contact {
    position: absolute;
    left: 686px;
    top: 22px;
    margin: 0;
    padding: 0;
    list-style: none;
    font-family: "Raleway", Arial, sans-serif;
    font-size: 15.5px;
    line-height: 26.5px;
    color: var(--text);
    letter-spacing: -0.2px;
  }
  .contact li {
    display: flex;
    align-items: center;
    gap: 9px;
  }
  .contact svg {
    width: 13px;
    height: 13px;
    fill: var(--text);
    flex: none;
  }
  .footer-band {
    position: absolute;
    left: 0;
    bottom: 0;
    width: 931px;
    height: 140px;
    background: linear-gradient(to bottom,
      rgba(140, 198, 63, 0) 0%,
      rgba(140, 198, 63, 0.55) 22%,
      var(--brand-blue) 55%,
      var(--brand-blue) 100%);
  }
  .doctor-name {
    position: absolute;
    right: 30px;
    top: 1124px;
    margin: 0;
    font-family: "Bitter", Georgia, serif;
    font-weight: 400;
    font-size: 31px;
    line-height: 38px;
    color: var(--paper);
    letter-spacing: 0.3px;
  }
</style>
</head>
<body>
<main class="letterhead">
  <header>
    <div class="practice-name">
      <div class="practice-name__dot"></div>
      <div>
        <span class="practice-name__title">Meridian</span>
        <span class="practice-name__sub">Endodontics P.C.</span>
      </div>
    </div>

    <address class="address">
      2748 Tollard Avenue<br>
      Suite K<br>
      West Tollard NY 14391
    </address>

    <div class="divider"></div>

    <ul class="contact">
      <li>
        <svg viewBox="0 0 16 16" aria-hidden="true"><path d="M4 1.5 6.5 4.5 5 6.3c.9 1.9 2.5 3.5 4.4 4.4L11.2 9.2l3 2.5-1.4 2.6c-.4.6-1.2.8-1.9.5C6.7 13 3 9.3 1.2 5.1.9 4.4 1.1 3.6 1.7 3.2Z"/></svg>
        716-392-5061
      </li>
      <li>
        <svg viewBox="0 0 16 16" aria-hidden="true"><path d="M4 1h6l2 2v3H4Z M1 7h14v6h-2v-2H3v2H1Z M4 12h8v3H4Z"/></svg>
        716-392-5087
      </li>
      <li>
        <svg viewBox="0 0 16 16" aria-hidden="true"><path d="M1 3h14v1.2L8 8.6 1 4.2Z M1 5.8l7 4.4 7-4.4V13H1Z"/></svg>
        oswickroot@mail.com
      </li>
    </ul>
  </header>

  <div class="footer-band" role="img" aria-label="Decorative green and blue wave band along the foot of the page"></div>

  <p class="doctor-name">Bertram L. Oswick, DDS</p>
</main>
</body>
</html>
```